Brookvale Estates LLC stationary for a real estate property management company.

Create stationary (letterhead, envelopes, business cards) using Brookvale Estates LLC logo as primary creative element. Stationary design needs to be horizontal, leaving as much space as possible for correspondence copy. See attached Creative Brief and past stationary files for details.

Target Market(s)

Prospective apartment residents and current residents, vendors, and government agencies.

Industry/Entity Type

Property Management

Contact Information for Business Card

Business card employee title: Property Manager. Should include address, phone, fax, email, website, slogan, and Brookvale Estates logo.

Font styles to use
Sans Serif

Colors
0592cd
000000

Requirements
Must have
• Tone should be conservative, institutional, business (i.e. banking, finance, real estate). Must include: address, phone, fax, website, and slogan (see attached Creative Brief). Should be a horizontal design, leaving as much room as possible for letter correspondence copy.
Nice to have
• Please use an Arial or Helvetica style font.
Should not have
• Letterhead layout should leave as much room as possible for copy.

```html
<!DOCTYPE html>
<html lang="en">
<head>
<meta charset="utf-8">
<title>Brookvale Estates LLC – Business Card</title>
<link rel="stylesheet" href="https://fonts.googleapis.com/css2?family=Arimo:wght@400;700&display=swap">
<style>
  :root {
    --brand-blue: #0f6aa8;
    --ink-grey: #4a4b4d;
    --text-grey: #58595b;
    --card-white: #f7f7f6;
    --back-light: #6c6d70;
    --back-dark: #3e3f42;
    --page-bg: #e6e4e1;
    --white: #ffffff;
  }
  * { margin: 0; padding: 0; box-sizing: border-box; }
  html, body { width: 1200px; height: 960px; overflow: hidden; }
  body {
    position: relative;
    background: var(--page-bg);
    font-family: "Arimo", Arial, Helvetica, sans-serif;
  }
  .card {
    position: absolute;
    width: 600px;
    height: 344px;
  }
  .card-front {
    left: 302px; top: 128px;
    background: var(--card-white);
  }
  .card-back {
    left: 299px; top: 488px;
    width: 602px; height: 342px;
    background: linear-gradient(135deg, var(--back-light) 0%, var(--back-dark) 45%, var(--back-dark) 100%);
  }
  .front-mark {
    position: absolute;
    left: 60px; top: 92px;
    width: 160px; height: 160px;
    border-radius: 50%;
    background: var(--brand-blue);
  }
  .front-details {
    position: absolute;
    right: 27px; top: 40px;
    text-align: right;
    color: var(--text-grey);
  }
  .company-name {
    color: var(--brand-blue);
    font-weight: 700;
    line-height: 1;
  }
  .company-name .name-main { display: block; font-size: 40px; letter-spacing: 0.5px; }
  .company-name .name-sub { display: block; font-size: 17px; letter-spacing: 3.2px; margin-top: 6px; }
  .person-name {
    margin-top: 16px;
    color: var(--brand-blue);
    font-weight: 700;
    font-size: 19px;
    line-height: 1;
  }
  .person-title { margin-top: 6px; font-size: 15px; }
  .address { margin-top: 13px; font-size: 13.5px; line-height: 1.4; }
  .contact { margin-top: 10px; font-size: 13.5px; line-height: 1.4; }
  .slogan {
    margin-top: 9px;
    color: var(--brand-blue);
    font-weight: 700;
    font-size: 14px;
  }
  .back-lockup {
    position: absolute;
    left: 0; right: 0; top: 0; bottom: 0;
    display: flex;
    align-items: center;
    justify-content: center;
    gap: 16px;
  }
  .back-mark {
    width: 70px; height: 70px;
    border-radius: 50%;
    background: var(--brand-blue);
  }
  .back-name {
    color: var(--white);
    font-weight: 700;
    line-height: 1;
  }
  .back-name .name-main { display: block; font-size: 44px; }
  .back-name .name-sub { display: block; font-size: 20px; letter-spacing: 4px; margin-top: 6px; }
</style>
</head>
<body>
  <section class="card card-front">
    <div class="front-mark"></div>
    <div class="front-details">
      <h1 class="company-name"><span class="name-main">BROOKVALE</span><span class="name-sub">ESTATES LLC</span></h1>
      <p class="person-name">DANIEL HARTLEY</p>
      <p class="person-title">Property Manager</p>
      <p class="address">2750 Alder Ridge Road #B210<br>Fairhaven, CA 90412</p>
      <p class="contact">Phone: 555-214-7730<br>Fax: 555-214-7731<br>daniel@brookvaleestates.us<br>www.brookvaleestates.us</p>
      <p class="slogan">Multifamily Property Management</p>
    </div>
  </section>

  <section class="card card-back">
    <div class="back-lockup">
      <div class="back-mark"></div>
      <h2 class="back-name"><span class="name-main">BROOKVALE</span><span class="name-sub">ESTATES LLC</span></h2>
    </div>
  </section>
</body>
</html>
```